Tech business card design

We need an amazing business card design for our new business 'Pexla' a marketing tech startup based in Sydney, Australia. We provide an online marketplace for businesses to search and buy advertising media, connect with service providers and learn more about marketing. We wish to communicate 'cool tech', reliability and professionalism and design based around our logo.

Target Market(s)

Business Owners

Contact Information for Business Card

Name
Position
Email Address
Website
Phone Number

Font styles to use
Other font styles liked:
• Avenir & Avenir Next

Colors

Designer to choose colors to be used in the design.

```html
<!DOCTYPE html>
<html lang="en">
<head>
<meta charset="utf-8">
<title>Pexla Business Card</title>
<link rel="stylesheet" href="https://fonts.googleapis.com/css2?family=Nunito+Sans:wght@300;400;600;800&display=swap">
<style>
  :root {
    --navy: #1d1b4c;
    --grey: #6d6d72;
    --light-grey: #9a9aa0;
    --card: #ffffff;
    --backdrop: #e4e4e7;
    --rule: #c9c9cd;
  }
  * { margin: 0; padding: 0; box-sizing: border-box; }
  html, body {
    width: 1200px; height: 892px; overflow: hidden;
    background: var(--backdrop);
    font-family: "Nunito Sans", "Avenir Next", Avenir, sans-serif;
  }
  .canvas {
    width: 1200px; height: 892px;
    display: flex; flex-direction: column;
    align-items: center; justify-content: center; gap: 60px;
  }
  .card {
    width: 600px; height: 343px;
    background: var(--card);
    box-shadow: 0 4px 18px rgba(0,0,0,0.12);
    position: relative;
  }
  .card-front {
    display: flex; flex-direction: column; align-items: center; justify-content: center;
  }
  .brand-name {
    font-weight: 800; font-size: 112px; line-height: 1;
    color: var(--navy); letter-spacing: -2px;
    margin-top: -10px;
  }
  .brand-url {
    margin-top: 42px;
    font-size: 13px; font-weight: 400;
    letter-spacing: 7px; color: var(--grey);
  }
  .card-back {
    display: flex; align-items: center; justify-content: center;
    padding-left: 40px;
  }
  .identity {
    text-align: right;
    padding-right: 22px;
  }
  .person-name {
    font-size: 20px; font-weight: 600; color: var(--navy);
    letter-spacing: 0.3px; line-height: 1.15;
  }
  .person-role {
    font-size: 16px; font-weight: 400; color: var(--grey);
    letter-spacing: 0.3px; line-height: 1.2;
  }
  .divider {
    width: 1px; height: 76px;
    background: linear-gradient(to bottom, transparent, var(--rule) 20%, var(--rule) 80%, transparent);
  }
  .contacts {
    list-style: none; padding-left: 22px;
  }
  .contact-item {
    display: flex; align-items: center; gap: 9px;
    font-size: 14px; color: var(--grey); line-height: 22px;
  }
  .contact-icon { width: 14px; height: 14px; flex: none; fill: var(--navy); }
</style>
</head>
<body>
<main class="canvas">
  <section class="card card-front" aria-label="Card front">
    <div class="brand-name">Pexla</div>
    <div class="brand-url">www.pexlamedia.com.au</div>
  </section>

  <section class="card card-back" aria-label="Card back">
    <div class="identity">
      <div class="person-name">DANIEL MARSH</div>
      <div class="person-role">FOUNDER, DIRECTOR</div>
    </div>
    <div class="divider"></div>
    <ul class="contacts">
      <li class="contact-item">
        <svg class="contact-icon" viewBox="0 0 14 14" aria-hidden="true">
          <path d="M3.5 0.5h7a1 1 0 0 1 1 1v11a1 1 0 0 1-1 1h-7a1 1 0 0 1-1-1v-11a1 1 0 0 1 1-1zM4 2v8.5h6V2zM6.3 11.3h1.4v1h-1.4z"/>
        </svg>
        +61 (0)412 555 019
      </li>
      <li class="contact-item">
        <svg class="contact-icon" viewBox="0 0 14 14" aria-hidden="true">
          <path d="M0.5 3h13v8.5h-13zM1.6 4l5.4 4 5.4-4v-0.2H1.6z" fill-rule="evenodd"/>
        </svg>
        daniel@pexlamedia.com.au
      </li>
      <li class="contact-item">
        <svg class="contact-icon" viewBox="0 0 14 14" aria-hidden="true">
          <circle cx="7" cy="7" r="6.3"/>
          <path d="M7 2.5v4.5h3" stroke="#fff" stroke-width="1.3" fill="none"/>
        </svg>
        www.pexlamedia.com.au
      </li>
    </ul>
  </section>
</main>
</body>
</html>
```